Web Design job - Condo Debts Collection Business needs a Web Design

I need a site for a client, who works with condo debts collection, and ensure all revenues provided by condo fees will be always available to the building manager of condo on a specific date, regardless of defaults.
I have the visual identity (logo, slogan and colors) of the company, and some requirements on layout (kind of slider, menu options, phone number on a noble position, etc) - maybe I can do a sketch, but I like the idea of give some freedom to designer.

*** PLEASE, we have no interest in templates. We want something new***

Target Market(s)

I have two targets for this design: - Condominium's building manager. This target is looking for a solution to overdue debts on it's condo. - Residents on condominiums. This target wants to live in a better place, where their neighbors pay their condominium fees on time.

Number of Pages Required

1 page

Requirements
Must have
• - Slider with title, some short text related, a nice image (I prefer happy and/or peaceful family, people doing business, happy friends, and so on).
• - I have a special attention to menu. I'm looking for one I can have a nice effect, more elegant, charming, kind of innovative.
• - Phone number on the top (or clearly visible).
• - Member log in area or icon on the top (or clearly visible).
• - News/articles area.
• - Modern fonts, with good quality, sans-serif on areas where reading is more intensive (prefer Google web-fonts).
• - Colors specified on attached files.
Nice to have
• - Clear background color, cause it's better to read larger texts (like articles). Dark backgrounds makes reading difficult.
• - A site with effects (like shadows, lines, curves, gradients, lights) is usually pretty.
• - I pay attention on beautiful footers.
Should not have
• - Images with a lot of money (I don't sell richness, I sell tranquility, peace, harmony, safety).
• - Poor menu.

```html
<!DOCTYPE html>
<html lang="en">
<head>
<meta charset="UTF-8">
<title>Vantio Cobrança Condominial</title>
<link rel="stylesheet" href="https://fonts.googleapis.com/css2?family=Montserrat:wght@400;500;600;700&family=Open+Sans:wght@400;600&display=swap">
<style>
:root{
  --gold:#e09a1e;
  --gold-light:#f2bd32;
  --gold-deep:#d48a12;
  --ink:#2b2b2b;
  --text:#3d3d3d;
  --muted:#6b6b6b;
  --paper:#ffffff;
  --stone:#efece7;
  --card-foot:#f1f1f1;
  --navy:#1d1d25;
}
*{box-sizing:border-box;margin:0;padding:0}
html,body{width:1200px;height:2773px;overflow:hidden}
body{position:relative;background:var(--paper);font-family:"Open Sans",Arial,sans-serif;color:var(--text)}
.abs{position:absolute}
.btn{display:inline-flex;align-items:center;justify-content:center;border-radius:30px;background:linear-gradient(180deg,var(--gold-light),var(--gold));font-family:"Montserrat",Arial,sans-serif;font-weight:700;color:var(--ink);box-shadow:0 4px 10px rgba(0,0,0,.18)}
/* header */
.top-phone{left:92px;top:28px;font-family:"Montserrat",sans-serif;font-weight:600;font-size:16px;color:var(--gold)}
.brand{left:520px;top:14px;display:flex;align-items:center;gap:10px}
.brand-dot{width:46px;height:46px;background:var(--gold);border-radius:4px}
.brand-name{font-family:"Montserrat",sans-serif;font-weight:700;font-size:40px;color:var(--ink);line-height:1}
.brand-sub{font-family:"Montserrat",sans-serif;font-weight:700;font-size:8px;color:var(--ink);letter-spacing:.5px;margin-top:2px}
.login{left:942px;top:15px;width:165px;height:47px;font-size:15px;color:#fff}
.nav{left:148px;top:81px;width:906px;height:52px;z-index:3;border-radius:26px;background:linear-gradient(180deg,var(--gold-light),var(--gold));box-shadow:0 5px 12px rgba(0,0,0,.25);display:flex;justify-content:center;align-items:center;gap:26px;font-family:"Montserrat",sans-serif;font-weight:700;font-size:16px;letter-spacing:1.5px;color:var(--ink)}
.nav span.sep{font-weight:500}
/* hero */
.hero{left:0;top:105px;width:1200px;height:700px}
.welcome{right:88px;top:355px;text-align:right;font-family:"Montserrat",sans-serif;color:var(--gold-light)}
.welcome h1{font-weight:400;font-size:35px;letter-spacing:.5px}
.welcome h1 b{font-weight:700}
.welcome h2{font-weight:700;font-size:26px;margin-top:12px;letter-spacing:.5px}
.welcome .btn{margin-top:28px;width:130px;height:40px;font-size:15px}
/* section headings */
.eyebrow{font-family:"Montserrat",sans-serif;font-weight:600;font-size:12px;color:var(--gold)}
.title{font-family:"Montserrat",sans-serif;font-weight:700;font-size:25px;color:var(--gold)}
.title::after{content:"";display:block;width:42px;height:3px;background:var(--gold);margin-top:10px}
/* about */
.about{left:111px;top:910px;width:450px}
.about .title{margin-top:14px}
.about p{margin-top:24px;font-size:15.5px;line-height:26px}
.about .btn{margin-top:36px;width:141px;height:47px;font-size:15px}
.video{left:619px;top:882px;width:476px;height:311px;box-shadow:12px 14px 18px rgba(0,0,0,.3)}
/* services */
.services-photo{left:0;top:1293px;width:612px;height:475px}
.services{left:612px;top:1293px;width:588px;height:475px;background:var(--stone);padding:75px 34px 0 34px}
.services > p{margin-top:20px;font-size:16px;line-height:27px;color:var(--ink)}
.svc-grid{display:grid;grid-template-columns:234px 234px;column-gap:0;row-gap:24px;margin-top:30px}
.svc h3{display:flex;align-items:center;gap:8px;font-family:"Montserrat",sans-serif;font-weight:700;font-size:16px;color:var(--gold)}
.svc p{margin-top:10px;font-size:12.5px;line-height:24px;color:var(--ink)}
/* blog */
.blog-title{left:0;top:1840px;width:1200px;text-align:center}
.blog-title .title::after{margin:12px auto 0}
.card{top:1936px;width:233px;height:316px;background:#fff;box-shadow:0 4px 12px rgba(0,0,0,.22);display:flex;flex-direction:column}
.card .ph{height:161px}
.card h4{padding:22px 10px 0;text-align:center;font-family:"Montserrat",sans-serif;font-weight:700;font-size:12px;color:var(--gold);height:56px;background:#f6f6f6}
.card p{padding:8px 18px 0;font-size:11.5px;line-height:19px;color:var(--ink);height:72px}
.card .more{flex:1;display:flex;align-items:center;justify-content:center;font-family:"Montserrat",sans-serif;font-weight:700;font-size:10.5px;background:var(--card-foot);color:var(--ink)}
.card .more.hot{color:var(--gold);background:#f6f6f6}
.view-all{left:1004px;top:2264px;width:100px;height:30px;font-size:10px}
/* footer */
.footer-wave{left:0;top:2300px;width:1200px;height:120px}
.footer{left:0;top:2415px;width:1200px;height:358px;background:var(--gold)}
.fcol{top:2476px}
.fcol h5{font-family:"Montserrat",sans-serif;font-weight:700;font-size:20px;color:var(--ink);letter-spacing:.3px}
.fcol ul{list-style:none;margin-top:22px}
.fcol li{font-size:12px;color:#fff;line-height:26px;display:flex;gap:12px;align-items:flex-start}
.fcol li svg{flex:none;margin-top:8px}
.email-field{margin-top:22px;width:262px;height:38px;background:#fff;border:1px solid #ddd;font-size:11.5px;color:var(--ink);padding:11px 14px}
.subscribe{margin-top:16px;width:136px;height:40px;border-radius:22px;background:var(--navy);color:#fff;font-family:"Montserrat",sans-serif;font-weight:600;font-size:13px;display:flex;align-items:center;justify-content:center}
.rule{left:98px;top:2681px;width:1004px;height:1px;background:rgba(255,255,255,.45)}
.copy{left:98px;top:2710px;font-size:12px;color:#fff}
.social{top:2703px;width:28px;height:28px;border-radius:50%}
</style>
</head>
<body>

<header>
  <div class="abs top-phone">Call us: (85) 3090.4417</div>
  <div class="abs brand">
    <span class="brand-dot"></span>
    <div>
      <div class="brand-name">vantio</div>
      <div class="brand-sub">COBRANÇA CONDOMINIAL</div>
    </div>
  </div>
  <a class="abs btn login">Member login</a>
  <nav class="abs nav">
    <span>HOME</span><span class="sep">|</span>
    <span>ABOUT US</span><span class="sep">|</span>
    <span>SERVICES</span><span class="sep">|</span>
    <span>BLOG</span><span class="sep">|</span>
    <span>CONTACT US</span>
  </nav>
</header>

<section>
  <svg class="abs hero" viewBox="0 0 1200 700" role="img" aria-label="Happy family flying a kite across a golden field at sunset">
    <defs>
      <linearGradient id="sky" x1="0" y1="0" x2="0" y2="1">
        <stop offset="0" stop-color="#8a8b8f"/>
        <stop offset=".35" stop-color="#e6c08a"/>
        <stop offset=".58" stop-color="#f5d49a"/>
        <stop offset=".7" stop-color="#8a6a3a"/>
        <stop offset="1" stop-color="#5a3d1f"/>
      </linearGradient>
      <radialGradient id="sun" cx=".2" cy=".55" r=".35">
        <stop offset="0" stop-color="#fff3d0" stop-opacity=".9"/>
        <stop offset="1" stop-color="#fff3d0" stop-opacity="0"/>
      </radialGradient>
    </defs>
    <path d="M0 0H1200V640C1100 610 1000 590 880 620C760 650 690 690 560 690C420 690 330 640 200 640C110 640 50 660 0 680Z" fill="url(#sky)"/>
    <path d="M0 0H1200V640C1100 610 1000 590 880 620C760 650 690 690 560 690C420 690 330 640 200 640C110 640 50 660 0 680Z" fill="url(#sun)"/>
  </svg>
  <div class="abs welcome">
    <h1>WELCOME TO <b>VANTIO</b></h1>
    <h2>COBRANCA CONDOMINIAL</h2>
    <a class="btn">Read More</a>
  </div>
</section>

<section>
  <div class="abs about">
    <div class="eyebrow">WHO WE ARE</div>
    <div class="title">ABOUT US</div>
    <p>Sed ut perspiciatis unde omnis iste natus error sit voluptatem accusantium doloremque laudantium, totam rem aperiam, eaque ipsa quae ab illo inventore veritatis et quasi architecto beatae vitae dicta sunt explicabo.</p>
    <a class="btn">READ MORE</a>
  </div>
  <svg class="abs video" viewBox="0 0 476 311" role="img" aria-label="Video: smiling family relaxing together on a sofa">
    <defs>
      <linearGradient id="vid" x1="0" y1="0" x2="0" y2="1">
        <stop offset="0" stop-color="#d9dfe3"/>
        <stop offset=".55" stop-color="#b9a698"/>
        <stop offset="1" stop-color="#3e4148"/>
      </linearGradient>
    </defs>
    <rect width="476" height="311" fill="url(#vid)"/>
    <circle cx="238" cy="156" r="22" fill="rgba(0,0,0,.35)"/>
    <path d="M231 144L249 156L231 168Z" fill="#fff"/>
  </svg>
</section>

<section>
  <svg class="abs services-photo" viewBox="0 0 612 475" role="img" aria-label="Businessman reviewing documents at a desk by a bright window">
    <defs>
      <radialGradient id="office" cx=".2" cy=".2" r=".9">
        <stop offset="0" stop-color="#fbf7f0"/>
        <stop offset=".45" stop-color="#b5aca3"/>
        <stop offset="1" stop-color="#2e2b2a"/>
      </radialGradient>
    </defs>
    <rect width="612" height="475" fill="url(#office)"/>
  </svg>
  <div class="abs services">
    <div class="title">OUR SERVICES</div>
    <p>Lorem ipsum dolor sit amet, consectetur adipisicing elit, sed do eiusmod tempor incididunt ut labore aliqua.</p>
    <div class="svc-grid">
      <div class="svc">
        <h3><svg width="26" height="18" viewBox="0 0 26 18"><rect x="1" y="1" width="24" height="16" rx="2" fill="none" stroke="#e09a1e" stroke-width="2"/><rect x="1" y="5" width="24" height="3" fill="#e09a1e"/></svg>LOREM IPSUM</h3>
        <p>Lorem ipsum dolor sit amet, consec tetur adipi sicing elit</p>
      </div>
      <div class="svc">
        <h3><svg width="26" height="18" viewBox="0 0 26 18"><rect x="1" y="1" width="24" height="16" rx="2" fill="none" stroke="#e09a1e" stroke-width="2"/><path d="M5 7H21M5 11H15" stroke="#e09a1e" stroke-width="2"/></svg>LOREM IPSUM</h3>
        <p>Lorem ipsum dolor sit amet, consec tetur adipi sicing elit</p>
      </div>
      <div class="svc">
        <h3><svg width="26" height="18" viewBox="0 0 26 18"><rect x="1" y="3" width="24" height="14" rx="2" fill="#e09a1e"/><circle cx="13" cy="10" r="4" fill="#fff"/></svg>LOREM IPSUM</h3>
        <p>Lorem ipsum dolor sit amet, consec tetur adipi sicing elit</p>
      </div>
      <div class="svc">
        <h3><svg width="26" height="18" viewBox="0 0 26 18"><rect x="1" y="1" width="24" height="16" rx="3" fill="none" stroke="#e09a1e" stroke-width="2"/><circle cx="13" cy="9" r="4" fill="none" stroke="#e09a1e" stroke-width="2"/></svg>LOREM IPSUM</h3>
        <p>Lorem ipsum dolor sit amet, consec tetur adipi sicing elit</p>
      </div>
    </div>
  </div>
</section>

<section>
  <div class="abs blog-title"><div class="title">FROM OUR BLOG</div></div>

  <article class="abs card" style="left:98px">
    <svg class="ph" viewBox="0 0 233 161" role="img" aria-label="Father and daughter playing at home"><rect width="233" height="161" fill="#e9ddd3"/></svg>
    <h4>LOREM IPSUM DOLOR SIT AMET</h4>
    <p>Lorem ipsum dolor sit amet, consecte-tur adipisicing elit, sed do eiusmod tempor incidid.</p>
    <div class="more hot">READ MORE »</div>
  </article>
  <article class="abs card" style="left:355px">
    <svg class="ph" viewBox="0 0 233 161" role="img" aria-label="Family reading together in a cozy tent with string lights"><rect width="233" height="161" fill="#6a4a32"/></svg>
    <h4>LOREM IPSUM DOLOR SIT AMET</h4>
    <p>Lorem ipsum dolor sit amet, consecte-tur adipisicing elit, sed do eiusmod tempor incidid.</p>
    <div class="more">READ MORE »</div>
  </article>
  <article class="abs card" style="left:612px">
    <svg class="ph" viewBox="0 0 233 161" role="img" aria-label="Family blowing bubbles in a sunny park"><rect width="233" height="161" fill="#b8b487"/></svg>
    <h4>LOREM IPSUM DOLOR SIT AMET</h4>
    <p>Lorem ipsum dolor sit amet, consecte-tur adipisicing elit, sed do eiusmod tempor incidid.</p>
    <div class="more">READ MORE »</div>
  </article>
  <article class="abs card" style="left:869px">
    <svg class="ph" viewBox="0 0 233 161" role="img" aria-label="Three generations of a family standing together outdoors"><rect width="233" height="161" fill="#9aa4a0"/></svg>
    <h4>LOREM IPSUM DOLOR SIT AMET</h4>
    <p>Lorem ipsum dolor sit amet, consecte-tur adipisicing elit, sed do eiusmod tempor incidid.</p>
    <div class="more">READ MORE »</div>
  </article>

  <a class="abs btn view-all">VIEW ALL</a>
</section>

<footer>
  <svg class="abs footer-wave" viewBox="0 0 1200 120" preserveAspectRatio="none">
    <path d="M0 60C200 10 420 0 640 30C860 60 1040 20 1200 50V120H0Z" fill="#ecc26f"/>
    <path d="M0 110C150 40 320 30 480 60C700 100 900 60 1200 20V120H0Z" fill="#e5ad44"/>
    <path d="M0 118C250 90 480 80 700 100C900 118 1050 110 1200 95V120H0Z" fill="#e09a1e"/>
  </svg>
  <div class="abs footer"></div>

  <div class="abs fcol" style="left:100px">
    <h5>CONTACT US</h5>
    <ul>
      <li><svg width="10" height="10" viewBox="0 0 10 10"><path d="M10 0L0 4L4 6L6 10Z" fill="#fff"/></svg><span>Av. Central das Palmeiras,<br>1.240 Sala 302, Ed.</span></li>
      <li><svg width="10" height="10" viewBox="0 0 10 10"><path d="M2 0L4 2.5L3 4C4 6 4.5 6.5 6 7L7.5 6L10 8L8.5 10C4 10 0 6 0 1.5Z" fill="#fff"/></svg><span>(85) 3090.4417</span></li>
      <li><svg width="11" height="9" viewBox="0 0 11 9"><rect width="11" height="9" fill="#fff"/><path d="M0 0L5.5 5L11 0" stroke="#e09a1e" fill="none"/></svg><span>contato@vantio.com.br</span></li>
    </ul>
  </div>
  <div class="abs fcol" style="left:357px">
    <h5>QUICK LINKS</h5>
    <ul>
      <li><svg width="6" height="8"><path d="M0 0L6 4L0 8Z" fill="#fff"/></svg>Home</li>
      <li><svg width="6" height="8"><path d="M0 0L6 4L0 8Z" fill="#fff"/></svg>AboutUs</li>
      <li><svg width="6" height="8"><path d="M0 0L6 4L0 8Z" fill="#fff"/></svg>Services</li>
      <li><svg width="6" height="8"><path d="M0 0L6 4L0 8Z" fill="#fff"/></svg>Blog</li>
      <li><svg width="6" height="8"><path d="M0 0L6 4L0 8Z" fill="#fff"/></svg>Contact</li>
    </ul>
  </div>
  <div class="abs fcol" style="left:588px">
    <h5>OTHER LINKS</h5>
    <ul>
      <li><svg width="6" height="8"><path d="M0 0L6 4L0 8Z" fill="#fff"/></svg>Company</li>
      <li><svg width="6" height="8"><path d="M0 0L6 4L0 8Z" fill="#fff"/></svg>Privacy Policy</li>
      <li><svg width="6" height="8"><path d="M0 0L6 4L0 8Z" fill="#fff"/></svg>Terms &amp; Conditions</li>
      <li><svg width="6" height="8"><path d="M0 0L6 4L0 8Z" fill="#fff"/></svg>Our Clients</li>
    </ul>
  </div>
  <div class="abs fcol" style="left:840px">
    <h5>NEWSLETTER</h5>
    <div class="email-field">Email ID</div>
    <div class="subscribe">SUBSCRIBE</div>
  </div>

  <div class="abs rule"></div>
  <div class="abs copy">Copyrights © 2018. Allrights Reserved.</div>
  <span class="abs social" style="left:990px;background:#1e4e9e"></span>
  <span class="abs social" style="left:1031px;background:#1aa3e0"></span>
  <span class="abs social" style="left:1072px;background:#a3281e"></span>
</footer>

</body>
</html>
```